We need UI/UX design for a public, informational website for The Copper Lantern.
The pages, structure, and content scope are already defined. Designers are required to work only on the UI/UX layout of these existing pages, focusing on clarity, hierarchy, spacing, and usability. Do not add, remove, rename, or reinterpret pages or content.
The website is strictly informational only. It must not include accounts, onboarding, payments, custody, escrow administration, marketplaces, dashboards, or any transactional functionality.
Scope of work
Apply UI/UX design to the predefined website pages
Design layout for text, images, notices, and sections
Ensure consistent components and layout patterns across page types
Optimize layouts for long form, compliance focused content
Content writing, page creation, and branding changes are out of scope.
Structure reference
The complete page list, hierarchy, and content definitions are provided in the technical documentation and must be treated as the primary source of truth.
A Figma link is provided only as a light visual reference for page existence and structure:
https://meadow-knot-48203956.plumsite.example/
Designers must rely on the documentation for in depth and authoritative reference.
Brand guidelines
The Copper Lantern has existing brand guidelines and official logos, including light and dark versions. These assets will be provided and must be followed exactly. Designers must not redesign, alter, or reinterpret the brand identity.
Look and feel direction
The desired visual direction is inspired by:
https://ledgerwaltz.example/
This reference is provided only to indicate:
Institutional and enterprise tone
Clean, modern typography
Strong hierarchy and generous whitespace
Editorial, content first layouts
Do not copy branding, layouts, components, or assets from the reference site.
Hero section direction
The hero section should follow a similar structural approach to the hero used on https://ledgerwaltz.example/
, meaning:
Strong editorial framing
Clear headline hierarchy
Calm, institutional first impression
However, the background video must be Abu Dhabi focused, not generic or global. The video should visually reflect:
Abu Dhabi skyline or architectural language
Institutional, sovereign, long term infrastructure tone
Clean, slow, cinematic motion
No promotional, marketing, or lifestyle visuals
The hero must remain informational, restrained, and credible. No hype. No calls to invest. No implied participation.
Constraints
One global primary CTA only: “Continue to Halvemark” (external)
All other interactions must be informational
No visuals or language implying offers, investment, eligibility, or participation
Clear separation between informational content and any external operational platforms
Deliverables
High fidelity UI/UX designs created in Figma, covering:
Desktop layouts
Tablet layouts where relevant
Mobile layouts
Complete Figma file(s) including:
All designed pages defined in the technical documentation
A reusable component library (headers, footers, cards, notice panels, forms, CTAs, typography styles, spacing system)
Clearly defined layout grids, spacing rules, and text styles
Proper use of components and variants, not detached frames
Designs prepared for developer handoff, including:
Clear layer naming and structure
Auto layout where appropriate
Consistent use of styles and components
Responsive behavior demonstrated within Figma
Notes or annotations only where necessary for clarity
No prototypes, interactions, or motion design beyond basic layout states, unless explicitly requested. The focus is static UI/UX clarity, not animation.
A detailed technical specification document and official brand assets will be provided.
Any designs delivered outside Figma, that alter structure or content, or that ignore the defined constraints, boundaries, or tone will be rejected.

```html
<!DOCTYPE html>
<html lang="en">
<head>
<meta charset="utf-8">
<title>The Copper Lantern — Governance Framework</title>
<link href="https://fonts.googleapis.com/css2?family=Manrope:wght@400;500;600;700&display=swap" rel="stylesheet">
<style>
:root{
  --backdrop:#bdbdbd;
  --ink:#0b0b0c;
  --paper:#ffffff;
  --mist:#f0f4f9;
  --card-mist:#eaf0f7;
  --muted:#5c6470;
  --accent:#3ab0f5;
  --cta-blue:#4db8ff;
  --line-dark:#2b2b2e;
  --on-dark-muted:#a8adb5;
}
*{box-sizing:border-box;margin:0;padding:0}
html,body{width:1200px;height:3713px;overflow:hidden;background:var(--backdrop);font-family:"Manrope",sans-serif;color:var(--ink)}
.page{position:absolute;left:81px;top:81px;width:1038px;height:3549px;background:var(--mist);overflow:hidden}
.abs{position:absolute}
.eyebrow{font-size:10px;color:var(--accent);font-weight:500}

/* hero */
.hero-bg{position:absolute;left:0;top:0}
.nav-brand{left:14px;top:28px;color:#fff;font-size:11px;font-weight:500;letter-spacing:.04em;white-space:nowrap}
.nav-links{top:20px;left:352px;color:#fff;font-size:10px}
.nav-links a{color:#fff;text-decoration:none;position:absolute;white-space:nowrap}
.nav-links .active{color:var(--accent)}
.btn-light{left:917px;top:12px;width:110px;height:19px;background:#fff;border-radius:10px;font-size:9px;display:flex;align-items:center;justify-content:center;color:var(--ink);font-weight:500}
.hero-title{left:0;width:1038px;top:340px;text-align:center;color:#fff;font-size:37px;font-weight:500;line-height:46px;letter-spacing:-.01em}
.hero-sub{left:0;width:1038px;top:440px;text-align:center;color:#e8ecf1;font-size:17px;line-height:26px}
.btn-outline{left:446px;top:511px;width:144px;height:24px;border:1.3px solid #fff;border-radius:12px;color:#fff;font-size:10.5px;display:flex;align-items:center;justify-content:center}

/* about */
.about-title{left:148px;top:727px;font-size:29px;line-height:32px;font-weight:500;width:370px}
.about-copy{left:148px;top:830px;width:360px;font-size:8.6px;line-height:14.5px}
.btn-dark{background:var(--ink);color:#fff;border-radius:13px;font-size:10px;display:flex;align-items:center;justify-content:center;font-weight:500}
.about-tile{top:712px;width:114px;height:213px;background:linear-gradient(180deg,#4b535c,#1e242b 70%,#0f1318)}
.about-tile p{position:absolute;left:13px;bottom:12px;color:#fff;font-size:10px;line-height:12px;width:95px}

/* role */
.center-head{left:0;width:1038px;text-align:center}
.role-card{top:1074px;width:231px;height:311px;background:var(--paper)}
.role-card .photo{height:141px;background:linear-gradient(180deg,#6d7681,#303840)}
.role-card h3{position:absolute;left:18px;top:156px;font-size:17px;font-weight:500}
.role-card .desc{position:absolute;left:18px;top:183px;width:195px;font-size:8px;line-height:12px;color:var(--muted)}
.meta{position:absolute;left:18px;font-size:8px;display:flex}
.meta dt{width:60px;color:var(--muted)}
.meta dd{font-weight:600}

/* framework */
.framework{left:0;top:1467px;width:1038px;height:631px;background:#000;color:#fff}
.fw-title{left:148px;top:101px;font-size:27px;font-weight:500}
.fw-sub{left:148px;top:148px;width:230px;font-size:8.6px;line-height:15px;color:#e3e6ea}
.fw-item{left:467px;width:423px;border-bottom:1px solid var(--line-dark);height:99px}
.fw-item .num{position:absolute;top:0;font-size:8px;color:var(--on-dark-muted)}
.fw-item h4{position:absolute;top:13px;font-size:17px;font-weight:500}
.fw-item p{position:absolute;top:42px;font-size:8.3px;line-height:12.5px;color:var(--on-dark-muted);width:415px}

.skyline{left:0;top:2098px;width:1038px;height:288px;background:linear-gradient(180deg,#2e2e2e 0%,#6e6e6e 45%,#9a9a9a 70%,#3a3a3a 100%)}

/* reviewers */
.reviewers{left:0;top:2386px;width:1038px;height:331px;background:var(--paper)}
.rv-card{top:117px;height:142px;background:var(--card-mist);padding:20px}
.rv-card h4{font-size:13px;font-weight:500;line-height:17px}
.rv-card p{margin-top:6px;font-size:8px;line-height:12.5px;color:var(--muted);width:115px}

/* why */
.why-item{width:330px;text-align:center}
.why-item h4{font-size:13px;font-weight:500}
.why-item p{margin-top:7px;font-size:8.2px;line-height:12.5px;color:var(--muted)}

/* cta */
.cta-text{left:0;width:1038px;text-align:center}
.cta-title{top:3123px;font-size:25px;line-height:30px;font-weight:500;text-transform:uppercase}

/* footer */
.footer{left:0;top:3311px;width:1038px;height:238px;background:#000;color:#fff}
.f-col{top:32px}
.f-col h5{font-size:9px;font-weight:500;margin-bottom:9px}
.f-col li{list-style:none;font-size:7.2px;line-height:16px;color:#d7dbe0}
.f-legal{left:192px;width:660px;font-size:7.2px;line-height:11px;color:#c7ccd2}
</style>
</head>
<body>
<div class="page">

  <!-- hero -->
  <svg class="hero-bg" width="1038" height="630" viewBox="0 0 1038 630" role="img" aria-label="Dusk photograph of the Abu Dhabi skyline with towers and highways">
    <defs>
      <linearGradient id="heroTone" x1="0" y1="0" x2="0" y2="1">
        <stop offset="0" stop-color="#5a5f66"/>
        <stop offset=".35" stop-color="#2f343b"/>
        <stop offset=".75" stop-color="#1f2328"/>
        <stop offset="1" stop-color="#3b3530"/>
      </linearGradient>
    </defs>
    <path d="M0 0H1038V517Q519 727 0 517Z" fill="url(#heroTone)"/>
  </svg>
  <div class="abs nav-brand">THE COPPER LANTERN</div>
  <nav class="abs nav-links">
    <a class="active" style="left:14px">Home</a>
    <a style="left:50px">Framework</a>
    <a style="left:122px">Projects</a>
    <a style="left:179px">Company</a>
    <a style="left:244px">Insights</a>
    <a style="left:299px">Contact</a>
  </nav>
  <div class="abs btn-light">Continue to Halvemark</div>
  <h1 class="abs hero-title">A Governance Framework for<br>Structured Project Oversight</h1>
  <p class="abs hero-sub">Clear boundaries. Institutional discipline. Transparent<br>structures for managing risk and accountability.</p>
  <div class="abs btn-outline">Learn the Framework</div>

  <!-- about -->
  <p class="abs eyebrow" style="left:148px;top:711px">About The Copper Lantern</p>
  <h2 class="abs about-title">From Governance Frameworks to Intelligent Infrastructure</h2>
  <p class="abs about-copy">The Copper Lantern is a governance and project origination group focused on defining structural standards for complex initiatives. We publish clear frameworks that explain role separation, accountability, and long-term oversight across governance, operations, and project-level execution.</p>
  <div class="abs btn-dark" style="left:148px;top:895px;width:113px;height:24px">Our Framework</div>
  <div class="abs about-tile" style="left:539px" role="img" aria-label="Tall glass tower photograph"><p>Clear Role Separation</p></div>
  <div class="abs about-tile" style="left:657px" role="img" aria-label="Aerial city district photograph"><p>Independent Oversight Principles</p></div>
  <div class="abs about-tile" style="left:776px" role="img" aria-label="Institutional building facade photograph"><p>Institutional-Grade Standards</p></div>

  <!-- role -->
  <p class="abs eyebrow center-head" style="top:1009px">Role Clarity</p>
  <h2 class="abs center-head" style="top:1026px;font-size:28px;font-weight:500">Understanding Our Role</h2>

  <article class="abs role-card" style="left:148px">
    <div class="photo" role="img" aria-label="Classical government building with columns"></div>
    <h3>Governance</h3>
    <p class="desc">We define structural frameworks, role boundaries, and oversight mechanisms. This is our domain.</p>
    <dl class="meta" style="top:231px"><dt>Category</dt><dd>Governance Framework</dd></dl>
    <dl class="meta" style="top:253px"><dt>Audience</dt><dd>Institutional &amp; Public Reference</dd></dl>
    <dl class="meta" style="top:276px"><dt>Disclosure</dt><dd>Informational Use Only *</dd></dl>
  </article>
  <article class="abs role-card" style="left:403px">
    <div class="photo" role="img" aria-label="Modern towers with palm trees"></div>
    <h3>Operations</h3>
    <p class="desc">Day-to-day execution and project management occur outside our organization, through Halvemark.</p>
    <dl class="meta" style="top:231px"><dt>Category</dt><dd>Governance Framework</dd></dl>
    <dl class="meta" style="top:253px"><dt>Audience</dt><dd>Institutional &amp; Public Reference</dd></dl>
    <dl class="meta" style="top:276px"><dt>Disclosure</dt><dd>Informational Use Only *</dd></dl>
  </article>
  <article class="abs role-card" style="left:659px">
    <div class="photo" role="img" aria-label="Waterfront skyline at dusk" style="background:linear-gradient(180deg,#5b6a82,#2a3448)"></div>
    <h3>Transactions</h3>
    <p class="desc">We do not facilitate, execute, or participate in any financial transactions or operational activities.</p>
    <dl class="meta" style="top:231px"><dt>Category</dt><dd>Governance Framework</dd></dl>
    <dl class="meta" style="top:253px"><dt>Audience</dt><dd>Institutional &amp; Public Reference</dd></dl>
    <dl class="meta" style="top:276px"><dt>Disclosure</dt><dd>Informational Use Only *</dd></dl>
  </article>

  <!-- framework -->
  <section class="abs framework">
    <p class="abs eyebrow" style="left:148px;top:75px">Core Governance Principles</p>
    <h2 class="abs fw-title">The Framework</h2>
    <p class="abs fw-sub">A structured set of principles defining oversight, accountability, and role separation.</p>
    <div class="abs fw-item" style="top:75px"><span class="num">01</span><h4>Role Boundaries</h4><p>Clear separation between governance responsibilities, operational platforms, and project-level execution to prevent overlap and ambiguity.</p></div>
    <div class="abs fw-item" style="top:174px"><span class="num">02</span><h4>SPV Structure</h4><p>Ring-fenced project structures designed to isolate liability, clarify accountability, and support disciplined execution.</p></div>
    <div class="abs fw-item" style="top:274px"><span class="num">03</span><h4>Escrow Model</h4><p>Independent escrow principles describing conditional release mechanisms and third-party oversight—without operational execution on this site.</p></div>
    <div class="abs fw-item" style="top:374px"><span class="num">04</span><h4>Records and Registers</h4><p>Standards for documentation, evidence records, and transparency to support auditability and structural clarity.</p></div>
    <div class="abs fw-item" style="top:474px"><span class="num">05</span><h4>Risk and Boundaries</h4><p>Defined limitation frameworks outlining scope, risk containment, and enforcement of governance boundaries.</p></div>
  </section>

  <div class="abs skyline" role="img" aria-label="Black and white panorama of a city skyline"></div>

  <!-- reviewers -->
  <section class="abs reviewers">
    <h2 class="abs center-head" style="top:66px;font-size:28px;font-weight:500">For Framework Reviewers</h2>
    <div class="abs rv-card" style="left:148px;width:169px"><h4>Review Governance Structures</h4><p>Explore published frameworks outlining governance models, role separation, and accountability principles.</p></div>
    <div class="abs rv-card" style="left:340px;width:168px"><h4>Defined Structural Ownership</h4><p>Frameworks clarify responsibility and authority boundaries without operational or transactional execution.</p></div>
    <div class="abs rv-card" style="left:530px;width:169px"><h4>Operational Independence</h4><p>Execution, asset handling, and platform operations occur outside this site through independent entities.</p></div>
    <div class="abs rv-card" style="left:720px;width:170px"><h4>Clear Access Boundaries</h4><p>This site provides documentation and reference materials only—no onboarding, custody, or execution.</p></div>
  </section>

  <!-- why -->
  <h2 class="abs center-head" style="top:2777px;font-size:27px;font-weight:500">Why The Copper Lantern</h2>
  <div class="abs why-item" style="left:163px;top:2844px"><h4>Governance-First Approach</h4><p>We prioritize structural clarity and accountability, treating governance as the foundation—not an afterthought.</p></div>
  <div class="abs why-item" style="left:544px;top:2844px"><h4>Proven Structural Principles</h4><p>Our frameworks are informed by institutional standards across governance, compliance, and long-term infrastructure design.</p></div>
  <div class="abs why-item" style="left:163px;top:2924px"><h4>Bridging Structure &amp; Execution</h4><p>We define governance and role boundaries while execution occurs independently through separate operational platforms.</p></div>
  <div class="abs why-item" style="left:544px;top:2924px"><h4>Defined Control &amp; Boundaries</h4><p>Clear limitations ensure responsibilities remain properly scoped, auditable, and enforceable.</p></div>

  <!-- cta -->
  <svg class="abs" style="left:0;top:3020px" width="1038" height="291" viewBox="0 3020 1038 291">
    <path d="M0 3145Q519 2949 1038 3145V3311H0Z" fill="var(--cta-blue)"/>
    <path d="M0 3141Q519 2945 1038 3141" fill="none" stroke="#000" stroke-width="4"/>
    <circle cx="519" cy="3045" r="11" fill="var(--mist)" stroke="#000" stroke-width="1.5"/>
    <path d="M514 3049L519 3040L524 3049Z" fill="none" stroke="#000" stroke-width="1.3"/>
  </svg>
  <p class="abs cta-text" style="top:3105px;font-size:9px;color:#eaf6ff">FOR PROJECT ORIGINATORS</p>
  <h2 class="abs cta-text cta-title">Define Your Project's<br>Governance Framework</h2>
  <p class="abs cta-text" style="top:3193px;font-size:10px;line-height:16px">Design clear structural roles, accountability boundaries, and oversight<br>principles before operational execution begins.</p>
  <div class="abs btn-dark" style="left:422px;top:3234px;width:190px;height:24px">Start a Framework Discussion</div>

  <!-- footer -->
  <footer class="abs footer">
    <div class="abs f-col" style="left:192px;width:150px">
      <h5>The Copper Lantern</h5>
      <ul><li style="line-height:11px">A governance framework for structured project oversight and risk management.</li></ul>
    </div>
    <div class="abs f-col" style="left:359px"><h5>Framework</h5><ul><li>Role Boundaries</li><li>SPV Structure</li><li>Escrow Model</li><li>Records and Registers</li><li>Risk and Boundaries</li></ul></div>
    <div class="abs f-col" style="left:527px"><h5>Company</h5><ul><li>About</li><li>Leadership</li><li>Governance</li><li>Press</li><li>Careers</li><li>Contact</li></ul></div>
    <div class="abs f-col" style="left:696px"><h5>Legal</h5><ul><li>Terms of Use</li><li>Privacy Policy</li><li>Cookie Policy</li><li>Disclaimer and Risk Notices</li><li>Acceptable Use</li><li>Accessibility</li></ul></div>
    <p class="abs f-legal" style="top:174px">© 2026 The Copper Lantern. All rights reserved.</p>
    <p class="abs f-legal" style="top:189px">This website provides informational content only. The Copper Lantern does not provide investment advice, execute projects, or facilitate transactions. All operational activities are conducted through Halvemark, a separate platform.</p>
  </footer>
</div>
</body>
</html>
```